Business Card Design For A Renovation Contractor Company

We need a business card for a new company based in Singapore, our company name is "RB Tolvane". We are a renovation contractor that builds designs into reality. We build more of F&B restaurants, retail stores and commercial offices. We work very closely with designers. The final design should communicate to our client that we are a company that you can trust, that will plan and complete your project without giving you a headache. I like my client to remember my company as "RB". The beauty of SIMPLE is important.

Industry/Entity Type

Contractor

Requirements
Nice to have
• Black or Red base

```html
<!DOCTYPE html>
<html lang="en">
<head>
<meta charset="utf-8">
<title>RB Tolvane — Business Card</title>
<link href="https://fonts.googleapis.com/css2?family=Open+Sans:wght@300;400;600;700&display=swap" rel="stylesheet">
<style>
  :root{
    --bg:#e4e4ea;
    --black:#0a0a0a;
    --white:#ffffff;
    --red:#e0121b;
    --ink:#1a1a1a;
    --rule:#d0d0d0;
  }
  *{margin:0;padding:0;box-sizing:border-box}
  html,body{width:1200px;height:987px;overflow:hidden}
  body{background:var(--bg);font-family:"Open Sans",Arial,sans-serif;position:relative}
  .card{position:absolute;left:300px;width:600px;height:343px;border-radius:28px;overflow:hidden;
        box-shadow:0 10px 28px rgba(0,0,0,.18)}
  .card--front{top:100px;background:var(--white)}
  .card--back{top:544px;background:var(--black)}
  .card__shapes{position:absolute;inset:0;width:100%;height:100%}

  .brand{position:absolute;left:58px;top:48px;width:250px}
  .brand__mark{display:flex;align-items:center;gap:12px}
  .brand__dot{width:34px;height:34px;border-radius:50%;background:var(--red);flex:none}
  .brand__name{font-size:40px;font-weight:400;color:var(--ink);letter-spacing:-1px;line-height:1;white-space:nowrap}
  .brand__tagline{margin-top:8px;padding-top:4px;border-top:1px solid var(--ink);
        font-size:15px;font-weight:300;color:var(--ink);letter-spacing:.3px;white-space:nowrap}

  .divider{position:absolute;left:322px;top:54px;width:1px;height:118px;background:var(--rule)}

  .contact{position:absolute;left:340px;top:60px;list-style:none;font-size:15px;color:var(--ink);line-height:22px}
  .contact li{display:flex;align-items:center;gap:8px;white-space:nowrap}
  .contact svg{width:13px;height:13px;flex:none}
  .contact .address--first{margin-top:4px}

  .person{position:absolute;right:36px;bottom:22px;text-align:right;color:var(--white)}
  .person__name{font-size:22px;font-weight:700;line-height:1.1}
  .person__title{font-size:14px;font-weight:400}

  .back-brand{position:absolute;left:0;right:0;top:120px;display:flex;justify-content:center;align-items:center;gap:18px}
  .back-brand__ring{width:56px;height:56px;border-radius:50%;border:6px solid var(--white)}
  .back-brand__name{font-size:54px;font-weight:400;color:var(--white);letter-spacing:-1px;line-height:1}
  .back-web{position:absolute;left:0;right:0;top:222px;text-align:center;color:var(--white);font-size:15px;letter-spacing:4px}
</style>
</head>
<body>

<section class="card card--front">
  <svg class="card__shapes" viewBox="0 0 600 343" preserveAspectRatio="none" aria-hidden="true">
    <path d="M0,70 C30,200 170,262 330,254 C430,249 520,262 600,300 L600,343 L0,343 Z" fill="var(--black)"/>
    <path d="M0,62 C22,190 160,246 320,240 C440,236 540,256 600,286 L600,300 C520,262 430,249 330,254 C170,262 30,200 0,70 Z" fill="var(--red)"/>
    <path d="M0,58 C20,186 158,242 320,236 L320,240 C160,246 22,190 0,62 Z" fill="var(--white)"/>
  </svg>

  <div class="brand">
    <div class="brand__mark">
      <span class="brand__dot"></span>
      <span class="brand__name">RB Tolvane</span>
    </div>
    <p class="brand__tagline">shaping spaces with a method</p>
  </div>

  <div class="divider"></div>

  <ul class="contact">
    <li><svg viewBox="0 0 12 12"><circle cx="6" cy="6" r="6" fill="var(--red)"/><path d="M4 3.2l1 1.4-.6.7c.4.9 1 1.5 1.9 1.9l.7-.6 1.4 1-.6 1.1C5.8 8.6 3.4 6.2 3 4z" fill="var(--white)"/></svg>123-456-0789</li>
    <li><svg viewBox="0 0 12 12"><rect x="3" y="0.5" width="6" height="11" rx="1.3" fill="var(--red)"/><rect x="4.2" y="2" width="3.6" height="6" fill="var(--white)"/></svg>123-456-0789</li>
    <li><svg viewBox="0 0 12 12"><rect x="0.5" y="2.5" width="11" height="7.5" rx="1" fill="var(--red)"/><path d="M1 3l5 4 5-4" stroke="var(--white)" fill="none"/></svg>info@rbtolvane.com</li>
    <li><svg viewBox="0 0 12 12"><circle cx="6" cy="6" r="5.5" fill="var(--red)"/><path d="M1 6h10M6 .5v11M6 .8c-2.5 3-2.5 7.4 0 10.4M6 .8c2.5 3 2.5 7.4 0 10.4" stroke="var(--white)" stroke-width=".8" fill="none"/></svg>www.rbtolvane.com</li>
    <li class="address address--first">Street Name, City Name</li>
    <li class="address">State Zip Code</li>
  </ul>

  <div class="person">
    <p class="person__name">Your Name</p>
    <p class="person__title">Title</p>
  </div>
</section>

<section class="card card--back">
  <div class="back-brand">
    <span class="back-brand__ring"></span>
    <span class="back-brand__name">RB Tolvane</span>
  </div>
  <p class="back-web">www.rbtolvane.com</p>
</section>

</body>
</html>
```